Electrical Contractor Brochure, Folder and Letter Head

Brightwell Power Ltd. is an Edmonton based electrical contractor focusing on commercial and industrial electrical services. Our target market is manufacturing facilities, warehouses and commercial buildings.

We want to seem larger than we are with service vehicles and electricians ready to dispatch to service calls and new installations. Our key color is the blue in the logo. The BWP logo is well branded in Edmonton and should be on the brochure.

We are looking for a tri-fold brochure, full-page brochure with folder sleeves and a letter head.
Updates

Please ignore the second page of copy.  I only want the electrical content in the brochure.  This is my mistake.  Please use only the first page of copy.

Industry/Entity Type

Electrical

Requirements
Must have
• Many background pics of the services, electricians and projects. I like the faded BWP logo in the background of the letterhead! Folder Size A4
Nice to have
• Try the pic named Cover Pic1 to on the front of the brochure.
Should not have
• DO NOT USE ANY WEBSITE CONTENT. THIS IS NOT OUR BUSINESS. PLEASE USE ONLY CONTENT AND COLOR FROM THE ATTACHED FILES!!

```html
<!DOCTYPE html>
<html lang="en">
<head>
<meta charset="utf-8">
<title>Brightwell Power Ltd. Letterhead</title>
<link href="https://fonts.googleapis.com/css2?family=Open+Sans:wght@400;700&display=swap" rel="stylesheet">
<style>
  :root {
    --brand-blue: #1a5fae;
    --ink: #333333;
    --swoosh: #2f2f2f;
    --rule: #c8c8c8;
    --ghost: #eef2f7;
    --paper: #ffffff;
  }
  * { margin: 0; padding: 0; box-sizing: border-box; }
  html, body { width: 1011px; height: 1200px; overflow: hidden; background: var(--paper); }
  .letterhead {
    position: relative;
    width: 1011px;
    height: 1200px;
    background: var(--paper);
    font-family: "Open Sans", sans-serif;
    color: var(--ink);
  }
  .brand-name {
    position: absolute;
    left: 73px;
    top: 80px;
    font-size: 32px;
    font-weight: 700;
    color: var(--brand-blue);
    letter-spacing: 0.2px;
    white-space: nowrap;
  }
  .contact {
    position: absolute;
    left: 801px;
    top: 58px;
    padding-left: 16px;
    border-left: 1px solid var(--rule);
    font-size: 14.5px;
    line-height: 19px;
    font-style: normal;
    white-space: nowrap;
  }
  .contact-address { margin-bottom: 13px; }
  .contact-line { display: flex; align-items: center; gap: 5px; }
  .contact-icon { width: 11px; height: 11px; fill: var(--brand-blue); flex: none; }
  .ghost-mark {
    position: absolute;
    left: 0;
    top: 520px;
    width: 1011px;
    text-align: center;
    font-size: 260px;
    font-weight: 700;
    line-height: 1;
    color: var(--ghost);
    letter-spacing: 6px;
  }
  .footer-band {
    position: absolute;
    left: 0;
    bottom: 0;
    width: 1011px;
    height: 110px;
  }
  .website {
    position: absolute;
    right: 58px;
    bottom: 24px;
    font-size: 15.5px;
    letter-spacing: 3.2px;
    color: var(--paper);
  }
</style>
</head>
<body>
<main class="letterhead">
  <div class="brand-name">Brightwell Power Ltd.</div>

  <address class="contact">
    <div class="contact-address">14 Ridgeline Park<br>Edmonton, AB</div>
    <div class="contact-line">
      <svg class="contact-icon" viewBox="0 0 12 12" aria-hidden="true"><path d="M3 1 L5 3.5 L4 5 C4.6 6.4 5.6 7.4 7 8 L8.5 7 L11 9 L9.8 11 C5 10.6 1.4 7 1 2.2 Z"/></svg>
      <span>780-555-0142</span>
    </div>
    <div class="contact-line">
      <svg class="contact-icon" viewBox="0 0 12 12" aria-hidden="true"><rect x="3" y="1" width="6" height="3"/><rect x="1" y="4.5" width="10" height="5" rx="1"/><rect x="3" y="8" width="6" height="3"/></svg>
      <span>780-555-0187</span>
    </div>
    <div class="contact-line">
      <svg class="contact-icon" viewBox="0 0 12 12" aria-hidden="true"><path d="M1 3 H11 V10 H1 Z M1.5 3.5 L6 7 L10.5 3.5" stroke="#fff" stroke-width="0.9"/></svg>
      <span>info@bwpower.ca</span>
    </div>
  </address>

  <div class="ghost-mark" aria-hidden="true">BWP</div>

  <svg class="footer-band" viewBox="0 0 1011 110" preserveAspectRatio="none" aria-hidden="true">
    <path d="M0 12 C220 72 560 74 1011 20 L1011 110 L0 110 Z" fill="var(--brand-blue)"/>
    <path d="M33 14 C250 62 620 52 968 12 C650 44 300 62 33 14 Z" fill="var(--swoosh)"/>
  </svg>
  <div class="website">www.bwpower.ca</div>
</main>
</body>
</html>
```